Professional violinist needs business cards

I am trying to attract the following jobs:
-private violin lessons (primarily classical)
-performance gigs (weddings, birthday parties, funerals, etc.)
-collaborations with other artists (studio recordings, performances)

I want to communicate that I have a very high standard of excellence for my work, but I also love people and celebrations.
Values/style words I like are:
love, joy, peace, fun, beauty, authenticity, excellence, warmth, refined/sleek, free spirited. If that's too confusing, just ignore :)

I will attach my favorite business card template that I could find on Canva. The lines are supposed to be like a music staff, which I think is really cool, but I also don't want it to look too busy. I like the simple black and white--I think it looks sharp--but I also am open to other ideas. I also have seen business cards with pictures included that looked great, so I attached an image that could be used as well.

I am also attaching a file that I made of my initials that could be used as a logo, but I'm not sure if it should be included.

Information on the card:
-My name (18 letters total)
-"violinist"
-phone number, email, website

Thank you!

```html
<!DOCTYPE html>
<html lang="en">
<head>
<meta charset="utf-8">
<title>Celia Marwood – Violinist Business Card</title>
<link href="https://fonts.googleapis.com/css2?family=Dancing+Script:wght@500&family=Cinzel:wght@400&family=Lora:wght@400&display=swap" rel="stylesheet">
<style>
  :root{
    --backdrop:#2b2b2c;
    --card:#23272c;
    --card-deep:#1d2024;
    --staff:#3c4249;
    --gold:#d3c2a0;
    --gold-bright:#c9a66b;
    --ink:#e9e6e0;
    --photo-dark:#3e3a33;
    --photo-mid:#6b6253;
  }
  *{margin:0;padding:0;box-sizing:border-box}
  html,body{width:1200px;height:1138px;overflow:hidden;background:var(--backdrop)}
  .canvas{position:relative;width:1200px;height:1138px}
  .card{
    position:absolute;left:274px;width:622px;height:374px;border-radius:14px;overflow:hidden;
    background:linear-gradient(160deg,var(--card) 0%,var(--card-deep) 100%);
  }
  .card--front{top:186px}
  .card--back{top:608px}
  .staff{position:absolute;left:0;width:100%;height:1px;background:var(--staff)}
  .wordmark{
    position:absolute;font-family:"Lora",serif;font-weight:400;color:var(--gold);
    font-size:22px;letter-spacing:1px;white-space:nowrap;transform:translateX(-50%);
  }
  .name{
    position:absolute;font-family:"Dancing Script",cursive;font-weight:500;color:var(--ink);
    font-size:38px;white-space:nowrap;transform:translateX(-50%);line-height:1;
  }
  .title{
    position:absolute;font-family:"Cinzel",serif;color:var(--ink);font-size:17px;
    letter-spacing:3px;white-space:nowrap;transform:translateX(-50%);line-height:1;
  }
  .title--ruled{display:flex;align-items:center;gap:14px}
  .title--ruled::before,.title--ruled::after{content:"";width:60px;height:1px;background:#8a8780}
  .photo-panel{position:absolute;left:0;top:0}
  .contacts{position:absolute;right:32px;top:242px;list-style:none}
  .contacts li{
    display:flex;justify-content:flex-end;align-items:center;gap:10px;
    font-family:"Lora",serif;font-size:14.5px;color:var(--ink);height:23.3px;
  }
  .contacts svg{width:13px;height:13px;fill:var(--gold)}
  .accent{color:var(--gold-bright)}
</style>
</head>
<body>
<main class="canvas">

  <section class="card card--front" aria-label="Card front">
    <div class="staff" style="top:92px"></div>
    <div class="staff" style="top:115px"></div>
    <div class="staff" style="top:138px"></div>
    <div class="staff" style="top:162px"></div>
    <div class="wordmark" style="left:311px;top:113px">Celia Marwood</div>
    <div class="name" style="left:311px;top:208px">Celia Marwood</div>
    <div class="title" style="left:311px;top:258px">VIOLINIST</div>
  </section>

  <section class="card card--back" aria-label="Card back">
    <svg class="photo-panel" width="300" height="374" viewBox="0 0 300 374">
      <defs>
        <linearGradient id="goldBand" x1="0" y1="0" x2="0" y2="1">
          <stop offset="0" stop-color="#d8b77a"/>
          <stop offset="1" stop-color="#8c6a3a"/>
        </linearGradient>
        <linearGradient id="photoTone" x1="0" y1="0" x2="1" y2="1">
          <stop offset="0" stop-color="var(--photo-mid)"/>
          <stop offset="1" stop-color="var(--photo-dark)"/>
        </linearGradient>
      </defs>
      <path d="M0 0 H244 C300 90 300 260 214 374 H0 Z" fill="url(#goldBand)"/>
      <path role="img" aria-label="Photo of the violinist holding her violin beside a stone wall"
            d="M0 0 H208 C275 100 280 270 212 374 H0 Z" fill="url(#photoTone)"/>
    </svg>

    <div class="wordmark" style="left:448px;top:64px">Celia Marwood</div>
    <div class="name" style="left:456px;top:128px">Celia Marwood</div>
    <div class="title title--ruled" style="left:456px;top:170px">VIOLINIST</div>

    <ul class="contacts">
      <li>+1 (555) 014-2287
        <svg viewBox="0 0 16 16" aria-hidden="true"><path d="M2 5c0-2 3-3 6-3s6 1 6 3v1h-3V5H5v1H2z M4 7h8l2 6H2z"/></svg></li>
      <li>Riverton, MD
        <svg viewBox="0 0 16 16" aria-hidden="true"><path d="M8 1a5 5 0 0 0-5 5c0 4 5 9 5 9s5-5 5-9a5 5 0 0 0-5-5zm0 7a2 2 0 1 1 0-4 2 2 0 0 1 0 4z"/></svg></li>
      <li><span>www.<span class="accent">CeliaMarwood</span>.com</span>
        <svg viewBox="0 0 16 16" aria-hidden="true"><circle cx="8" cy="8" r="7"/><path d="M1 8h14M8 1v14M3 4h10M3 12h10" stroke="#23272c" stroke-width="1" fill="none"/></svg></li>
      <li>Celia@CeliaMarwood.com
        <svg viewBox="0 0 16 16" aria-hidden="true"><path d="M1 3h14v10H1z"/><path d="M1 3l7 6 7-6M1 13l5-5M15 13l-5-5" stroke="#23272c" stroke-width="1.2" fill="none"/></svg></li>
    </ul>
  </section>

</main>
</body>
</html>
```